Volbrey Inc Business Card

Looking to get an updated business card for a Contract Machining company (www.volbreyinc.example) - looking for a clean design the portrays the technical nature of the business - colors can follow the website design and be in any combination that makes sense (red black, white, metallic or silver) - logos attached for use also. Would like space for: Name, title, business phone (555 214-3086), cell phone , website (www.volbreyinc.example) - possibly QR code could be integrated for website (designer choice), business address - 418 Harlow Bend, Brackenfield, Lorvane 48199 (cards will be for 4 employees, I will either need to modify a template or I can provide individual information)
Target Market(s)
Aerospace, defense and medical device manufacturing companies that need machining
Industry/Entity Type
Machining for aerospace, defense, medical
Contact Information for Business Card
Name, Title, Business Phone, Cell Phone, email, business website and business address
Look and feel

```html
<!DOCTYPE html>
<html lang="en">
<head>
<meta charset="utf-8">
<title>Volbrey Inc Business Card</title>
<link rel="stylesheet" href="https://fonts.googleapis.com/css2?family=Montserrat:wght@400;500;700;800&display=swap">
<style>
  :root {
    --brand-red: #b41f26;
    --brand-red-dark: #8e161c;
    --ink: #1c1c1c;
    --paper: #ffffff;
    --stage: #e9e6e2;
  }
  * { box-sizing: border-box; margin: 0; padding: 0; }
  html, body { width: 1200px; height: 931px; overflow: hidden; background: var(--stage); }
  .stage { position: relative; width: 1200px; height: 931px; font-family: "Montserrat", sans-serif; }

  .card {
    position: absolute; width: 700px; height: 400px; border-radius: 22px;
    overflow: hidden; box-shadow: 0 10px 28px rgba(0,0,0,.22);
  }
  .card-back { left: 60px; top: 45px; background: var(--brand-red); }
  .card-front { left: 440px; top: 486px; background: var(--paper); color: var(--ink); }

  .back-pattern {
    position: absolute; inset: 0;
    background: radial-gradient(circle at 10% 55%, #d2545a 0%, var(--brand-red) 40%, var(--brand-red-dark) 100%);
  }
  .back-mark {
    position: absolute; left: 560px; top: 150px; width: 80px; height: 80px;
    border-radius: 50%; background: var(--paper);
  }

  .brand-circle {
    position: absolute; left: 505px; top: 25px; width: 160px; height: 160px;
    border-radius: 50%; background: var(--brand-red);
  }
  .brand-name {
    position: absolute; right: 36px; top: 192px;
    font-weight: 800; font-size: 30px; letter-spacing: 1px; color: var(--brand-red);
  }
  .main-rule {
    position: absolute; left: 40px; right: 36px; top: 240px;
    height: 2px; background: var(--brand-red);
  }
  .person-name {
    position: absolute; left: 40px; top: 200px;
    font-weight: 700; font-size: 30px; color: var(--brand-red);
  }
  .person-title {
    position: absolute; left: 40px; top: 248px; font-size: 15px; font-weight: 500;
  }
  .title-rule {
    position: absolute; left: 40px; top: 272px; width: 190px; height: 2px; background: var(--brand-red);
  }
  .contact-list { position: absolute; left: 40px; top: 284px; list-style: none; }
  .contact-list li {
    display: flex; align-items: center; gap: 10px; height: 26px; font-size: 15px;
  }
  .contact-list svg { width: 16px; height: 16px; fill: var(--brand-red); flex: none; }
  .address {
    position: absolute; right: 36px; top: 282px; text-align: right;
    font-size: 14px; line-height: 1.45; font-style: normal;
  }
</style>
</head>
<body>
<main class="stage">
  <section class="card card-back" aria-label="Card back">
    <div class="back-pattern" role="img" aria-label="Repeating field of embossed brand circles in red tones"></div>
    <div class="back-mark"></div>
  </section>

  <section class="card card-front" aria-label="Card front">
    <div class="brand-circle"></div>
    <div class="brand-name">VOLBREY</div>
    <div class="person-name">Dana Whitfield</div>
    <div class="main-rule"></div>
    <div class="person-title">Owner</div>
    <div class="title-rule"></div>
    <ul class="contact-list">
      <li><svg viewBox="0 0 16 16"><path d="M3 1l3 3-1.6 2a9 9 0 0 0 5.6 5.6L12 10l3 3-2 2.5C6.5 15 1 9.5.5 3z"/></svg>555 214-3086</li>
      <li><svg viewBox="0 0 16 16"><path d="M1 5c2-3 12-3 14 0v2h-4V5.5H5V7H1z"/><rect x="2" y="8" width="12" height="7" rx="1"/></svg>555 214-3086</li>
      <li><svg viewBox="0 0 16 16"><path d="M1 3h14v1L8 9 1 4z"/><path d="M1 5.5l7 5 7-5V13H1z"/></svg>info@volbreyinc.example</li>
      <li><svg viewBox="0 0 16 16"><circle cx="8" cy="8" r="7"/></svg>www.volbreyinc.example</li>
    </ul>
    <address class="address">418 Harlow Bend,<br>Brackenfield, Lorvane 48199</address>
  </section>
</main>
</body>
</html>
```